Verdana Crest New Website - Online Learning and Education

New Wordpress website for an online learning site that has courses, worksheets, quizzes, etc.
Updates

We would like something similar to this website: https://hallowaybridgeinstitute.example/mediation-skills-course/. But continue with the content of our current website: http://verdanacrestlearninghub.example

We would like something similar to this site: https://hallowaybridgeinstitute.example/mediation-skills-course/

Coding

Coded - Design and coding required

```html
<!DOCTYPE html>
<html lang="en">
<head>
<meta charset="utf-8">
<title>Verdana Crest – Online Learning</title>
<link href="https://fonts.googleapis.com/css2?family=Merriweather:ital,wght@0,400;0,700;1,400;1,700&family=Montserrat:wght@400;600;700&display=swap" rel="stylesheet">
<style>
:root{
  --red:#b0091f;
  --navy:#1d3466;
  --ink:#333;
  --muted:#666;
  --grey:#4a4a4a;
  --footer:#1b1b1b;
  --white:#fff;
  --serif:'Merriweather',Georgia,serif;
  --sans:'Montserrat',Arial,sans-serif;
}
*{box-sizing:border-box;margin:0;padding:0}
html,body{width:1200px;height:3222px;overflow:hidden;background:#fff}
body{position:relative;font-family:var(--serif);color:var(--ink)}
.abs{position:absolute}

/* header */
.site-header{position:absolute;left:0;top:0;width:1200px;height:91px;background:#fff}
.brand{left:112px;top:22px;display:flex;align-items:center;gap:12px}
.brand-mark{width:40px;height:40px;border-radius:50%;background:var(--navy)}
.brand-name{font-family:var(--serif);font-weight:700;font-size:30px;color:var(--navy);letter-spacing:.5px}
.login{left:722px;top:33px;display:flex;align-items:center;gap:10px;font-size:15px;color:#666}
.header-search{left:831px;top:24px;width:256px;height:43px;border:1px solid #bbb;font-size:14px;color:#777;padding:12px 22px}
.header-search svg{position:absolute;right:16px;top:12px}

.main-nav{position:absolute;left:0;top:91px;width:1200px;height:69px;background:var(--red)}
.main-nav a{position:absolute;top:24px;color:#fff;font-size:16px;text-decoration:none}
.social{position:absolute;display:flex;gap:13px}
.social span{width:31px;height:31px;border:1.5px solid #fff;border-radius:50%;display:flex;align-items:center;justify-content:center}
.social span::after{content:"";width:9px;height:9px;border-radius:50%;background:#fff}

/* hero */
.hero{position:absolute;left:0;top:160px;width:1200px;height:558px;
  background:linear-gradient(110deg,#3b3a38 0%,#6e665d 35%,#8b8279 60%,#4b4641 100%)}
.hero::after{content:"";position:absolute;inset:0;background:rgba(20,20,20,.35)}
.hero-inner{position:absolute;inset:0;z-index:1;text-align:center;color:#fff}
.hero h1{position:absolute;left:0;width:1200px;top:120px;font-size:68px;font-weight:700;letter-spacing:-.5px}
.hero h1 em{font-style:italic;font-weight:400}
.hero p{position:absolute;left:270px;width:660px;top:224px;font-size:16px;line-height:26px}
.hero-search{position:absolute;left:270px;top:310px;width:659px;height:67px;border:2px solid #fff;text-align:left;padding:22px 27px;font-size:16px}
.hero-search .bar{position:absolute;left:588px;top:8px;width:2px;height:48px;background:#fff}
.hero-search svg{position:absolute;left:609px;top:24px}

/* features */
.feature{position:absolute;top:666px;width:240px;text-align:center}
.feature .ring{margin:0 auto;width:108px;height:108px;border-radius:50%;background:#fff;box-shadow:0 3px 10px rgba(0,0,0,.2);display:flex;align-items:center;justify-content:center}
.feature .dot{width:60px;height:60px;border-radius:50%;background:var(--grey);display:flex;align-items:center;justify-content:center}
.feature h3{margin-top:24px;font-size:19px;font-weight:400;color:#444}
.feature p{margin-top:12px;font-size:14.5px;line-height:24px;color:#666}
.feature.active .dot{background:var(--navy)}
.feature.active h3{color:var(--navy)}

/* section headings */
.section-title{position:absolute;left:0;width:1200px;text-align:center;font-size:48px;font-weight:400;color:var(--red)}
.section-title::before,.section-title::after{content:"-";display:inline-block;margin:0 28px;font-weight:700}
.section-title.light{color:#fff}

/* categories */
.category{position:absolute;width:296px;height:201px;overflow:hidden}
.category .photo{position:absolute;inset:0}
.category span{position:absolute;left:16px;bottom:12px;color:#fff;font-size:25px;font-weight:700}
.category.current span{bottom:20px}
.category.current span::after{content:"";position:absolute;left:0;bottom:-12px;width:105px;height:3px;background:#fff}

/* popular */
.popular{position:absolute;left:0;top:1617px;width:1200px;height:576px;background:var(--red)}
.course{position:absolute;top:219px;width:207px;height:231px;background:#fff;border:2px solid #fff}
.course .photo{height:132px}
.course h4{margin:22px 0 0 12px;font-size:15.5px;font-weight:700;color:#222}
.course p{margin:10px 0 0 12px;font-size:12px;line-height:20px;color:#777;width:180px}
.arrow{position:absolute;top:327px;width:34px;height:34px;border-radius:50%;background:#fff;display:flex;align-items:center;justify-content:center}

/* news */
.news{position:absolute;top:2392px;width:386px;height:321px;border:1px solid #ccc;background:#fff}
.news .photo{height:224px}
.news .date{position:absolute;left:22px;top:231px;width:74px;height:75px;background:var(--red);color:#fff;text-align:center}
.news .date b{display:block;font-size:26px;font-weight:400;margin-top:10px}
.news .date i{font-size:12.5px}
.news h4{position:absolute;left:113px;top:237px;font-size:15.5px;font-weight:400;color:var(--red)}
.news p{position:absolute;left:113px;top:259px;width:260px;font-size:14.5px;line-height:22px;color:#777}

/* footer */
.site-footer{position:absolute;left:0;top:2806px;width:1200px;height:416px;background:var(--footer);color:#fff}
.site-footer h5{position:absolute;top:50px;font-size:21px;font-weight:400}
.site-footer .txt{position:absolute;font-family:var(--sans);font-size:13px;line-height:26px;color:#eee}
.nl-input{position:absolute;left:502px;top:159px;width:273px;height:37px;border:2px solid #fff;border-radius:20px;font-family:var(--sans);font-size:12.5px;padding:9px 22px}
.nl-btn{position:absolute;left:504px;top:218px;width:141px;height:36px;border-radius:20px;background:var(--red);font-family:var(--sans);font-weight:700;font-size:15px;text-align:center;line-height:36px}
.contact{position:absolute;left:843px;display:flex;gap:16px;font-family:var(--sans);font-size:14.5px;line-height:24px}
.contact svg{flex:none;margin-top:4px}
.copy{position:absolute;left:0;top:378px;width:1200px;text-align:center;font-size:16px}
</style>
</head>
<body>

<header class="site-header">
  <div class="abs brand"><div class="brand-mark"></div><div class="brand-name">Verdana Crest</div></div>
  <div class="abs login">
    <svg width="24" height="24" viewBox="0 0 24 24" fill="none" stroke="#1d3466" stroke-width="1.8"><path d="M7 5a9 9 0 1 1 0 14"/><path d="M2 12h12M10 8l4 4-4 4"/></svg>
    Login
  </div>
  <div class="abs header-search">Search
    <svg width="18" height="18" viewBox="0 0 18 18" fill="none" stroke="#888" stroke-width="1.6"><circle cx="7.5" cy="7.5" r="6"/><path d="M12 12l5 5"/></svg>
  </div>
</header>

<nav class="main-nav">
  <a style="left:142px">Home</a>
  <a style="left:224px">Courses</a>
  <a style="left:321px">Instructors</a>
  <a style="left:444px">Events</a>
  <a style="left:532px">Faq</a>
  <a style="left:596px">Elements</a>
  <div class="social" style="left:922px;top:19px"><span></span><span></span><span></span><span></span></div>
</nav>

<section class="hero" role="img" aria-label="Photo of a woman working on a laptop at a home desk">
  <div class="hero-inner">
    <h1>Search for <em>your Course</em></h1>
    <p>Nemo enim ipsam voluptatem quia voluptas sit aspernatur aut odit aut fugit, sed quia consequuntur magni dolores eos qui ratione voluptatem sequi nesciunt.</p>
    <div class="hero-search">Keywords<div class="bar"></div>
      <svg width="18" height="18" viewBox="0 0 18 18" fill="none" stroke="#fff" stroke-width="1.6"><circle cx="7.5" cy="7.5" r="6"/><path d="M12 12l5 5"/></svg>
    </div>
  </div>
</section>

<div class="feature" style="left:98px">
  <div class="ring"><div class="dot"><svg width="26" height="24" viewBox="0 0 26 24" fill="none" stroke="#fff" stroke-width="1.6"><rect x="2" y="2" width="22" height="15"/><path d="M9 22h8M13 17v5M6 13l5-5 4 3 5-5"/></svg></div></div>
  <h3>Software</h3>
  <p>Duis aute irure dolor in reprehenderit in voluptate velit esse cillum dolore eu</p>
</div>
<div class="feature active" style="left:350px">
  <div class="ring"><div class="dot"><svg width="28" height="20" viewBox="0 0 28 20" fill="none" stroke="#fff" stroke-width="1.6"><path d="M2 2h24l-4 8 4 8H2z"/><text x="7" y="14" fill="#fff" stroke="none" font-size="8" font-family="Arial" font-weight="700">EN</text></svg></div></div>
  <h3>Business English</h3>
  <p>Duis aute irure dolor in reprehenderit in voluptate velit esse cillum dolore eu</p>
</div>
<div class="feature" style="left:603px">
  <div class="ring"><div class="dot"><svg width="26" height="24" viewBox="0 0 26 24" fill="none" stroke="#fff" stroke-width="1.6"><path d="M3 10v6h4l9 5V4L7 10z"/><path d="M20 8l3-2M20 13h4M20 17l3 2"/></svg></div></div>
  <h3>Marketing</h3>
  <p>Duis aute irure dolor in reprehenderit in voluptate velit esse cillum dolore eu</p>
</div>
<div class="feature" style="left:856px">
  <div class="ring"><div class="dot"><svg width="26" height="26" viewBox="0 0 26 26" fill="none" stroke="#fff" stroke-width="1.6"><path d="M2 9L13 3l11 6z M3 24h20M5 11v10M10 11v10M16 11v10M21 11v10"/></svg></div></div>
  <h3>Banking Courses</h3>
  <p>Duis aute irure dolor in reprehenderit in voluptate velit esse cillum dolore eu</p>
</div>

<h2 class="section-title" style="top:990px">Course Categories</h2>

<div class="category" style="left:130px;top:1102px"><div class="photo" role="img" aria-label="Hands typing on a laptop with a city overlay" style="background:linear-gradient(135deg,#3e5370,#1f2f47)"></div><span>Finance</span></div>
<div class="category current" style="left:445px;top:1102px"><div class="photo" role="img" aria-label="Woman reviewing architectural plans on a monitor" style="background:linear-gradient(135deg,#6b6a68,#2b2521)"></div><span>Architecture</span></div>
<div class="category" style="left:759px;top:1102px"><div class="photo" role="img" aria-label="Hand touching a digital network of images" style="background:linear-gradient(135deg,#24303a,#3d6b70)"></div><span>Distribution</span></div>
<div class="category" style="left:130px;top:1322px"><div class="photo" role="img" aria-label="Tablet controlling industrial robot arms" style="background:linear-gradient(135deg,#2b4566,#6783a3)"></div><span>Production</span></div>
<div class="category" style="left:445px;top:1322px"><div class="photo" role="img" aria-label="Person typing on a laptop by a window" style="background:linear-gradient(135deg,#b7b3ad,#5a514a)"></div><span>E Commerce</span></div>
<div class="category" style="left:759px;top:1322px"><div class="photo" role="img" aria-label="Team watching a video conference in a meeting room" style="background:linear-gradient(135deg,#d3d3d1,#4a4c50)"></div><span>HRM</span></div>

<section class="popular">
  <h2 class="section-title light" style="top:100px">Popular Courses</h2>
  <div class="arrow" style="left:-13px"><svg width="10" height="14" viewBox="0 0 10 14" fill="none" stroke="#333" stroke-width="1.6"><path d="M3 2l5 5-5 5"/></svg></div>
  <div class="arrow" style="left:1179px"><svg width="10" height="14" viewBox="0 0 10 14" fill="none" stroke="#333" stroke-width="1.6"><path d="M7 2L2 7l5 5"/></svg></div>
  <div class="course" style="left:150px"><div class="photo" role="img" aria-label="Group of students around a laptop" style="background:linear-gradient(135deg,#8a5a3b,#3c2a22)"></div><h4>Web Designing</h4><p>Nemo enim ipsam voluptatem quia voluptas sit</p></div>
  <div class="course" style="left:381px"><div class="photo" role="img" aria-label="Student working in a library" style="background:linear-gradient(135deg,#a88a6a,#4b4b52)"></div><h4>Research Studies</h4><p>Nemo enim ipsam voluptatem quia voluptas sit</p></div>
  <div class="course" style="left:613px"><div class="photo" role="img" aria-label="Man holding a tablet in an office" style="background:linear-gradient(135deg,#c9cdd2,#5a5f66)"></div><h4>Engineering</h4><p>Nemo enim ipsam voluptatem quia voluptas sit</p></div>
  <div class="course" style="left:844px"><div class="photo" role="img" aria-label="Woman working on a laptop at a desk" style="background:linear-gradient(135deg,#d7d2cc,#6b5d52)"></div><h4>Business Analytics</h4><p>Nemo enim ipsam voluptatem quia voluptas sit</p></div>
</section>

<h2 class="section-title" style="top:2285px">Latest News</h2>

<article class="news" style="left:205px">
  <div class="photo" role="img" aria-label="Woman with headphones using a laptop" style="background:linear-gradient(135deg,#e4e1dc,#8a7a6c)"></div>
  <div class="date"><b>10</b><i>May 2019</i></div>
  <h4>Nemo enim ipsam voluptatem</h4>
  <p>Duis aute irure dolor in reprehenderit in voluptate velit esse cillum</p>
</article>
<article class="news" style="left:609px">
  <div class="photo" role="img" aria-label="Man with headphones waving at a laptop" style="background:linear-gradient(135deg,#b39a7c,#3f3a36)"></div>
  <div class="date"><b>10</b><i>May 2019</i></div>
  <h4>Nemo enim ipsam voluptatem</h4>
  <p>Duis aute irure dolor in reprehenderit in voluptate velit esse cillum</p>
</article>

<footer class="site-footer">
  <h5 style="left:111px">About Us</h5>
  <p class="txt" style="left:112px;top:111px;width:340px">Nemo enim ipsam voluptatem quia voluptas sit aspernatur aut odit aut fugit, sed quia consequuntur magni dolores eos qui ratione voluptatem sequi nesciunt. Neque porro quisquam est, qui dolorem ipsum quia dolor sit amet, consectetur, adipisci velit, sed quia non numquam eius modi tempora incidunt ut labore et</p>

  <h5 style="left:503px">Sign Up For Newsletter</h5>
  <p class="txt" style="left:504px;top:111px;width:290px;font-size:13px;line-height:22px">excepteur sint occaecat cupidatat non proident, sunt in culpa qui officia deserunt</p>
  <div class="nl-input">Enter email</div>
  <div class="nl-btn">SUBSCRIBE</div>

  <h5 style="left:841px;top:52px">Contact Us</h5>
  <div class="contact" style="top:115px">
    <svg width="16" height="20" viewBox="0 0 16 20"><path d="M8 0a7 7 0 0 0-7 7c0 5 7 13 7 13s7-8 7-13a7 7 0 0 0-7-7zm0 10a3 3 0 1 1 0-6 3 3 0 0 1 0 6z" fill="#fff"/></svg>
    <span>#10,&nbsp; Duis aute irure dolor in<br>reprehenderit</span>
  </div>
  <div class="contact" style="top:174px">
    <svg width="18" height="18" viewBox="0 0 18 18"><path d="M4 1l3 4-2 2c1 2.5 3.5 5 6 6l2-2 4 3-2 3C8 17 1 10 1 3z" fill="#fff"/></svg>
    <span>Phone:<br>&nbsp;&nbsp;555-014-2387</span>
  </div>
  <div class="contact" style="top:240px">
    <svg width="18" height="14" viewBox="0 0 18 14"><path d="M0 2l9 6 9-6V0H0zM0 4v10h18V4l-9 6z" fill="#fff"/></svg>
    <span>Email:<br>info@verdanacrest.example</span>
  </div>

  <div class="social" style="left:528px;top:333px;gap:6px"><span></span><span></span><span></span><span></span></div>
  <div class="copy">Copyrights &nbsp;© 2019 &nbsp;| &nbsp;All Rights Reserved</div>
</footer>

</body>
</html>
```